Bright Harbor Counseling Letterhead for hip modern business

I would like some ombre use of the colors in the logo hip letterhead that incorporates logo colors and feel, needs to connect with young professionals and college students. i need to be able to write letters to schools to excuse absences as well. i like color blocks on one side preferably using colors from the attached logo design.

Target Market(s)

high income young people, young adults and college students

Industry/Entity Type

mental health

Font styles to use
Serif
Sans Serif

Colors
0054AA
0677BA
7BADD7
CADEEF
E8F1F8
0094D4
00A9DD
6FCCEA
C7EBF8
E9F6FB
00AB8E
00BBA5
67D7C9
C6EFE9
E9F9F6
59FF00
82FF00
B8FF75
E3FFCB
F4FFEA
A7469A
B969AE
D3A5CF
EDDBEB
F8F0F9
6B429C
8869AF
B7A5CE
E3DAEB
F3F0F8

Requirements
Must have
• a modern hip feel, somewhat color

```html
<!DOCTYPE html>
<html lang="en">
<head>
<meta charset="utf-8">
<title>Bright Harbor Counseling – Letterhead</title>
<link rel="stylesheet" href="https://fonts.googleapis.com/css2?family=Questrial&family=Arimo:wght@400&display=swap">
<style>
  :root {
    --backdrop: #ece9e5;
    --paper: #ffffff;
    --ink: #1f1f1f;
    --body-ink: #555555;
    --muted: #666666;
    --teal: #00bba5;
    --teal-soft: #67d7c9;
    --blue: #0677ba;
    --sky: #00a9dd;
    --magenta: #a7469a;
    --orchid: #b969ae;
    --purple: #8869af;
    --purple-deep: #6b429c;
  }
  * { box-sizing: border-box; margin: 0; padding: 0; }
  html, body { width: 1200px; height: 900px; overflow: hidden; }
  body {
    background: var(--backdrop);
    display: flex;
    align-items: center;
    justify-content: center;
  }
  .letterhead {
    position: relative;
    width: 666px;
    height: 860px;
    background: var(--paper);
    box-shadow: 0 4px 18px rgba(0,0,0,0.12);
    overflow: hidden;
  }

  /* Header */
  .brand {
    position: absolute;
    left: 32px;
    top: 70px;
    display: flex;
    align-items: flex-start;
    gap: 10px;
    font-family: "Questrial", sans-serif;
    color: var(--ink);
    font-weight: 400;
  }
  .brand-dot {
    width: 14px; height: 14px;
    border-radius: 50%;
    background: var(--purple);
    margin-top: 9px;
  }
  .brand-name { display: flex; flex-direction: column; align-items: flex-end; }
  .brand-name .primary { font-size: 29px; line-height: 1; letter-spacing: 0.5px; }
  .brand-name .secondary { font-size: 14px; letter-spacing: 3px; margin-top: 4px; }

  .contact {
    position: absolute;
    left: 426px;
    top: 50px;
    padding-left: 6px;
    border-left: 1.5px solid var(--teal);
    font-family: "Questrial", sans-serif;
    font-size: 11.5px;
    color: var(--muted);
    line-height: 16px;
  }
  .contact-item { display: flex; align-items: center; gap: 4px; }
  .contact-item svg { width: 10px; height: 10px; flex: none; }

  .header-rule {
    position: absolute;
    left: 0; right: 0; top: 142px;
    height: 1.5px;
    background: linear-gradient(to right, var(--teal-soft) 0 42%, var(--purple) 42% 100%);
  }

  /* Body */
  .letter-body {
    position: absolute;
    left: 41px;
    right: 40px;
    top: 170px;
  }
  .letter-title {
    font-family: "Questrial", sans-serif;
    font-weight: 400;
    font-size: 23px;
    color: var(--ink);
    margin-bottom: 10px;
  }
  .letter-body p {
    font-family: "Arimo", sans-serif;
    font-size: 9.6px;
    line-height: 13px;
    color: var(--body-ink);
    text-align: justify;
  }
  .letter-body p.gap { margin-top: 26px; }

  .signature {
    position: absolute;
    right: 40px;
    top: 682px;
    width: 236px;
    height: 56px;
    background: linear-gradient(to right, rgba(31,31,31,0.06), rgba(31,31,31,0.12));
    border-bottom: 1px solid #333;
  }

  /* Footer band */
  .footer-band {
    position: absolute;
    left: 0; right: 0; bottom: 0;
    height: 110px;
    background:
      linear-gradient(to bottom, rgba(255,255,255,0) 0%, rgba(255,255,255,0) 30%),
      linear-gradient(to right, var(--blue) 0%, var(--magenta) 22%, var(--sky) 42%, var(--orchid) 62%, var(--blue) 80%, var(--magenta) 100%);
    -webkit-mask-image: linear-gradient(to bottom, rgba(0,0,0,0.35), #000 45%);
    mask-image: linear-gradient(to bottom, rgba(0,0,0,0.35), #000 45%);
  }
</style>
</head>
<body>
  <main class="letterhead">
    <header>
      <div class="brand">
        <span class="brand-dot" aria-hidden="true"></span>
        <div class="brand-name">
          <span class="primary">Bright Harbor</span>
          <span class="secondary">Counseling</span>
        </div>
      </div>

      <address class="contact" style="font-style:normal">
        <div class="contact-item">
          <svg viewBox="0 0 10 10" aria-hidden="true"><circle cx="5" cy="5" r="5" fill="var(--blue)"/><path d="M3.2 2.6l1 1-.5.6c.4.8.9 1.3 1.6 1.6l.6-.5 1 1-.6.8C4.6 7 3 5.4 2.6 3.2z" fill="#fff"/></svg>
          <span>555-014-2086</span>
        </div>
        <div class="contact-item">
          <svg viewBox="0 0 10 10" aria-hidden="true"><circle cx="5" cy="5" r="5" fill="var(--purple)"/><rect x="2.6" y="3.3" width="4.8" height="3.4" fill="none" stroke="#fff" stroke-width="0.8"/><path d="M2.6 3.3L5 5.2l2.4-1.9" fill="none" stroke="#fff" stroke-width="0.8"/></svg>
          <span>hello@brightharbor.com</span>
        </div>
        <div class="contact-item">
          <svg viewBox="0 0 10 10" aria-hidden="true"><circle cx="5" cy="5" r="5" fill="var(--magenta)"/><path d="M5 2.3a1.8 1.8 0 0 1 1.8 1.8C6.8 5.4 5 7.6 5 7.6S3.2 5.4 3.2 4.1A1.8 1.8 0 0 1 5 2.3z" fill="#fff"/><circle cx="5" cy="4.1" r="0.6" fill="var(--magenta)"/></svg>
          <span>14 Harbor Lane, Portside, box 40210</span>
        </div>
      </address>
      <div class="header-rule" aria-hidden="true"></div>
    </header>

    <section class="letter-body">
      <h1 class="letter-title">Lorem ipsum</h1>
      <p>Lorem ipsum dolor sit amet, consectetuer adipiscing elit, sed diam nonummy nibh euismod tincidunt ut laoreet dolore magna aliquam erat volutpat. Ut wisi enim ad minim veniam, quis nostrud exerci tation ullamcorper suscipit lobortis nisl ut aliquip ex ea commodo consequat. Duis autem vel eum iriure dolor in hendrerit in vulputate velit esse molestie consequat, vel illum dolore eu feugiat nulla facilisis at vero eros et accumsan et iusto odio dignissim qui blandit praesent luptatum zzril delenit augue duis dolore te feugait nulla facilisi.</p>
      <p class="gap">Lorem ipsum dolor sit amet, cons ectetuer adipiscing elit, sed diam nonummy nibh euismod tincidunt ut laoreet dolore magna aliquam erat volutpat. Ut wisi enim ad minim veniam, quis nostrud exerci tation ullamcorper suscipit lobortis nisl ut aliquip ex ea commodo consequat. Lorem ipsum dolor sit amet, consectetuer adipiscing elit, sed diam nonummy nibh euismod tincidunt ut laoreet dolore magna aliquam erat volutpat. Ut wisi enim ad minim veniam, quis nostrud exerci tation ullamcorper suscipit lobortis nisl ut aliquip ex ea commodo consequat. Duis autem vel eum iriure dolor in hendrerit in vulputate velit esse molestie consequat, vel illum dolore eu feugiat nulla facilisis at vero eros et accumsan et iusto odio dignissim qui blandit praesent luptatum zzril delenit augue duis dolore te feugait nulla facilisi.</p>
      <p>Lorem ipsum dolor sit amet, cons ectetuer adipiscing elit, sed diam nonummy nibh euismod tincidunt ut laoreet dolore magna aliquam erat volutpat. Ut wisi enim ad minim veniam, quis nostrud exerci tation ullamcorper suscipit lobortis nisl ut aliquip ex ea commodo consequat.</p>
      <p class="gap">Lorem ipsum dolor sit amet, consectetuer adipiscing elit, sed diam nonummy nibh euismod tincidunt ut laoreet dolore magna aliquam erat volutpat. Ut wisi enim ad minim veniam, quis nostrud exerci tation ullamcorper suscipit lobortis nisl ut aliquip ex ea commodo consequat. Duis autem vel eum iriure dolor in hendrerit in vulputate velit esse molestie consequat, vel illum dolore eu feugiat nulla facilisis at vero eros et accumsan et iusto odio dignissim qui blandit praesent luptatum zzril delenit augue duis dolore te feugait nulla facilisi. Lorem ipsum dolor sit amet, cons ectetuer adipiscing elit, sed diam nonummy nibh euismod tincidunt ut laoreet dolore magna aliquam erat volutpat. Ut wisi enim ad minim veniam, quis nostrud exerci tation ullamcorper suscipit lobortis nisl ut aliquip ex ea commodo consequat. Lorem ipsum dolor sit amet, consectetuer adipiscing elit, sed diam nonummy nibh euismod tincidunt ut laoreet dolore magna aliquam erat volutpat. Ut wisi enim ad minim veniam, quis nostrud exerci tation ullamcorper suscipit lobortis nisl ut aliquip ex ea commodo consequat. Duis autem vel eum iriure dolor in hendrerit in vulputate velit esse molestie consequat, vel illum dolore eu feugiat nulla facilisis at vero eros et accumsan et iusto odio dignissim qui blandit praesent luptatum zzril delenit augue duis dolore te feugait nulla facilisi.</p>
      <p class="gap">Lorem ipsum dolor sit amet, cons ectetuer adipiscing elit, sed diam nonummy nibh euismod tincidunt ut laoreet dolore magna aliquam erat volutpat. Ut wisi enim ad minim veniam, quis nostrud exerci tation ullamcorper suscipit lobortis nisl ut aliquip ex ea commodo consequat.</p>
    </section>

    <div class="signature" role="img" aria-label="Handwritten signature of the counselor"></div>

    <footer class="footer-band" role="img" aria-label="Decorative band of overlapping blue, teal, pink and purple translucent circles"></footer>
  </main>
</body>
</html>
```